"Harbor Builders" is a residential building company and needs a new business card design and may re

We would like a redesign based on the existing logo, and would like to see a new font as well. We are bespoke home builders who build sustainable energy efficient homes.

Industry/Entity Type

Construction

Contact Information for Business Card

Business card size 40mm x 90mm

Colors

Designer to choose colors to be used in the design.

```html
<!DOCTYPE html>
<html lang="en">
<head>
<meta charset="utf-8">
<title>Harbor Builders – Business Card</title>
<link rel="stylesheet" href="https://fonts.googleapis.com/css2?family=Ubuntu:wght@500;700&family=Arimo:wght@400;700&display=swap">
<style>
  :root {
    --backdrop: #3b3b3b;
    --gold: #9a7d35;
    --card-white: #f3f3f3;
    --text-grey: #6e6e6e;
    --swoosh-grey: #8d8e91;
    --white: #ffffff;
  }
  * { margin: 0; padding: 0; box-sizing: border-box; }
  html, body { width: 1200px; height: 960px; overflow: hidden; }
  body {
    position: relative;
    background: var(--backdrop);
    font-family: "Arimo", Arial, sans-serif;
  }
  .card {
    position: absolute;
    left: 270px;
    width: 660px;
    height: 376px;
    overflow: hidden;
  }
  .card-front { top: 73px; background: var(--gold); }
  .card-back { top: 510px; background: var(--card-white); }

  .front-wordmark {
    position: absolute;
    left: 0; right: 0; top: 250px;
    text-align: center;
    font-family: "Ubuntu", sans-serif;
    font-weight: 700;
    font-size: 50px;
    letter-spacing: 1px;
    color: var(--white);
  }
  .front-web {
    position: absolute;
    left: 0; right: 0; top: 332px;
    text-align: center;
    font-size: 15px;
    color: var(--white);
  }
  .front-web strong { font-weight: 700; }

  .back-wordmark {
    position: absolute;
    left: 52px; top: 102px;
    font-family: "Ubuntu", sans-serif;
    font-weight: 700;
    font-size: 34px;
    color: var(--gold);
  }
  .rule {
    position: absolute;
    left: 52px; top: 189px;
    width: 345px; height: 1.5px;
    background: var(--gold);
  }
  .person-name {
    position: absolute;
    left: 411px; top: 179px;
    font-family: "Ubuntu", sans-serif;
    font-weight: 700;
    font-size: 19px;
    letter-spacing: 0.4px;
    color: var(--gold);
  }
  .name-tab {
    position: absolute;
    left: 640px; top: 174px;
    width: 20px; height: 34px;
    background: var(--gold);
  }
  .address {
    position: absolute;
    left: 52px; top: 203px;
    font-size: 15px;
    line-height: 22px;
    color: var(--text-grey);
  }
  .contact-list {
    position: absolute;
    left: 52px; top: 253px;
    list-style: none;
    font-size: 15px;
    color: var(--text-grey);
  }
  .contact-list li {
    display: flex;
    align-items: center;
    height: 21px;
  }
  .contact-list svg { width: 14px; height: 14px; margin-right: 10px; flex: none; }
  .footer-swoosh { position: absolute; left: 0; bottom: 0; width: 660px; height: 62px; }
  .registration {
    position: absolute;
    right: 46px; top: 341px;
    font-size: 14px;
    color: var(--white);
  }
</style>
</head>
<body>

<section class="card card-front" aria-label="Card front">
  <div class="front-wordmark">Harbor Builders</div>
  <p class="front-web">www.<strong>harborbuilders</strong>.com.au</p>
</section>

<section class="card card-back" aria-label="Card back">
  <div class="back-wordmark">Harbor Builders</div>

  <div class="rule"></div>
  <h1 class="person-name">DANIEL MORETTI</h1>
  <div class="name-tab"></div>

  <p class="address">PO Box 2210 Northgate<br>LPO Eastvale WA 6100</p>

  <ul class="contact-list">
    <li>
      <svg viewBox="0 0 14 14" aria-hidden="true"><path fill="#6e6e6e" d="M1 5c0-2 2-3 6-3s6 1 6 3v1h-3V4.5H4V6H1zM3 7h8l2 5H1z"/></svg>
      0400 555 018
    </li>
    <li>
      <svg viewBox="0 0 14 14" aria-hidden="true"><rect x="1" y="3" width="12" height="8.5" fill="none" stroke="#6e6e6e" stroke-width="1.3"/><path d="M1 3l6 5 6-5" fill="none" stroke="#6e6e6e" stroke-width="1.3"/></svg>
      daniel@harborbuilders.com.au
    </li>
    <li>
      <svg viewBox="0 0 14 14" aria-hidden="true"><g fill="none" stroke="#6e6e6e" stroke-width="1.2"><circle cx="7" cy="7" r="5.8"/><ellipse cx="7" cy="7" rx="2.5" ry="5.8"/><path d="M1.2 7h11.6M2 4h10M2 10h10"/></g></svg>
      www.harborbuilders.com.au
    </li>
  </ul>

  <svg class="footer-swoosh" viewBox="0 0 660 62" preserveAspectRatio="none" aria-hidden="true">
    <path d="M0 62 C120 20 380 -5 660 20 L660 26 C400 4 150 25 20 62 Z" fill="var(--swoosh-grey)"/>
    <path d="M100 62 C260 22 460 12 660 30 L660 62 Z" fill="var(--gold)"/>
  </svg>
  <p class="registration">Registration 40518 ABN: 12 345 678 901</p>
</section>

</body>
</html>
```